Looking for someone to design a business card for my plumbing business Quandor Plumbing Solutions I want the background also to be black, must attract clients. If possible I want the front to be the logo and the back to show maybe the details.

Target Market(s)

Clients

Industry/Entity Type

Plumbing maintenance

Contact Information for Business Card

Name: Felix, Contact: 0461 539 207, Email: quandorplumbingsolutions@mailbrook.example, Licence number 728093K

Font styles to use
Other font styles liked:
• as per logo maybe?

Colors

Designer to choose colors to be used in the design.

Requirements
Nice to have
• stating the service I provide, emergency plumbing, plumbing maintenance, drainage maintenance, block sewer and stormwater, camera and locating.

```html
<!DOCTYPE html>
<html lang="en">
<head>
<meta charset="utf-8">
<title>Quandor Plumbing Solutions – Business Card</title>
<link rel="stylesheet" href="https://fonts.googleapis.com/css2?family=Montserrat:wght@400;500;600;700&display=swap">
<style>
  :root {
    --page-bg: #161616;
    --card-bg: #1f1f1f;
    --brand-blue: #4a8fd0;
    --text-light: #f2f2f2;
    --text-soft: #e6e6e6;
    --shade-deep: #181818;
    --shade-lift: #2c2c2c;
  }
  * { box-sizing: border-box; margin: 0; padding: 0; }
  html, body {
    width: 1200px;
    height: 1059px;
    overflow: hidden;
    background: var(--page-bg);
    font-family: "Montserrat", sans-serif;
  }
  .canvas {
    position: relative;
    width: 1200px;
    height: 1059px;
  }
  .card {
    position: absolute;
    background: var(--card-bg);
    border-radius: 22px;
    overflow: hidden;
  }
  .card--details { left: 257px; top: 89px; width: 687px; height: 390px; }
  .card--brand   { left: 254px; top: 547px; width: 693px; height: 393px; }

  .mascot-area {
    position: absolute;
    left: 350px; top: 16px;
    width: 330px; height: 356px;
    border-radius: 48% 40% 30% 36%;
    background: radial-gradient(ellipse at 55% 30%, var(--shade-lift) 0%, var(--shade-deep) 60%, rgba(24,24,24,0) 78%);
  }

  .name-bar {
    position: absolute;
    left: 0; top: 60px;
    width: 17px; height: 36px;
    background: var(--brand-blue);
  }
  .person-name {
    position: absolute;
    left: 40px; top: 55px;
    font-size: 27px;
    font-weight: 700;
    letter-spacing: 0.5px;
    color: var(--brand-blue);
    line-height: 1;
  }
  .person-role {
    position: absolute;
    left: 40px; top: 82px;
    font-size: 15.5px;
    font-weight: 400;
    color: var(--text-light);
  }
  .licence {
    position: absolute;
    left: 40px; top: 142px;
    font-size: 15.5px;
    color: var(--text-light);
  }
  .contact-list {
    position: absolute;
    left: 40px; top: 176px;
    list-style: none;
  }
  .contact-item {
    display: flex;
    align-items: center;
    height: 26px;
    font-size: 15.5px;
    color: var(--text-light);
  }
  .contact-icon {
    width: 13px; height: 13px;
    margin-right: 7px;
    flex: none;
  }
  .social-dot {
    width: 12px; height: 12px;
    border-radius: 50%;
    background: var(--brand-blue);
    margin-right: 8px;
    flex: none;
  }
  .services {
    position: absolute;
    left: 40px; top: 276px;
    font-size: 15.5px;
    color: var(--text-soft);
    line-height: 24px;
  }
  .service-row { display: flex; gap: 11px; }
  .service { display: flex; align-items: center; }
  .service::before {
    content: "";
    width: 5px; height: 5px;
    border-radius: 50%;
    background: var(--brand-blue);
    margin-right: 7px;
  }

  .brand-mark {
    position: absolute;
    left: 0; right: 0; top: 0; bottom: 0;
    display: flex;
    align-items: center;
    justify-content: center;
    gap: 14px;
  }
  .brand-dot {
    width: 26px; height: 26px;
    border-radius: 50%;
    background: var(--brand-blue);
  }
  .brand-name {
    font-size: 30px;
    font-weight: 700;
    color: var(--text-light);
    letter-spacing: 0.5px;
  }
</style>
</head>
<body>
<main class="canvas">

  <section class="card card--details">
    <div class="mascot-area" role="img" aria-label="Faint brand mascot silhouette holding a pipe wrench"></div>

    <span class="name-bar"></span>
    <h1 class="person-name">FELIX</h1>
    <p class="person-role">Founder &amp; CEO</p>

    <p class="licence">Licence number 728093K</p>

    <ul class="contact-list">
      <li class="contact-item">
        <svg class="contact-icon" viewBox="0 0 24 24" aria-hidden="true">
          <path fill="#4a8fd0" d="M6.6 10.8a15.1 15.1 0 0 0 6.6 6.6l2.2-2.2c.3-.3.7-.4 1-.2 1.1.4 2.3.6 3.6.6.6 0 1 .4 1 1V20c0 .6-.4 1-1 1A17 17 0 0 1 3 4c0-.6.4-1 1-1h3.5c.6 0 1 .4 1 1 0 1.3.2 2.5.6 3.6.1.3 0 .7-.2 1z"/>
        </svg>
        0461 539 207
      </li>
      <li class="contact-item">
        <svg class="contact-icon" viewBox="0 0 24 24" aria-hidden="true">
          <rect x="1" y="4" width="22" height="16" fill="#4a8fd0"/>
          <path d="M1 4l11 9 11-9" fill="none" stroke="#1f1f1f" stroke-width="2"/>
        </svg>
        quandorplumbingsolutions@mailbrook.example
      </li>
      <li class="contact-item">
        <span class="social-dot"></span>
        @QuandorPlumbingSolutions
      </li>
    </ul>

    <div class="services">
      <div class="service-row">
        <span class="service">Emergency plumbing</span>
        <span class="service">Plumbing maintenance</span>
      </div>
      <div class="service-row">
        <span class="service">Drainage maintenance</span>
        <span class="service">Camera and locating</span>
      </div>
      <div class="service-row">
        <span class="service">Block sewer and stormwater</span>
      </div>
    </div>
  </section>

  <section class="card card--brand">
    <div class="brand-mark">
      <span class="brand-dot"></span>
      <span class="brand-name">Quandor Plumbing Solutions</span>
    </div>
  </section>

</main>
</body>
</html>
```